Social Media App Needs PPT Template

We need a PowerPoint template for a new social media company based in the DC area called "Bold Ledger." We provide an interactive digital platform for executives to share actionable advice. We would like to see designs that use our orange logo color as an accent, but are mainly grey, white, and black. The final design should communicate clean, chic, modern, and professional.

Target Market(s)

Executives

Industry/Entity Type

Information Technology

Font styles to use
Sans Serif

Colors
f78f20
fbe7d2
ffffff
000000
e8e8e8
757575

Requirements
Must have
• My project must have title page and many options for the body of the ppt (graphs, tables, etc). It also needs to be easy to modify. I must have someone who is experienced in creating powerpoint templates.
Nice to have
• It would be nice to have a very modern and clean design that includes the logo on every page, but still leaves a lot of room for the content of the slide
Should not have
• My design project should not look to busy.

```html
<!DOCTYPE html>
<html lang="en">
<head>
<meta charset="utf-8">
<title>Bold Ledger – Content Slide</title>
<link rel="stylesheet" href="https://fonts.googleapis.com/css2?family=Lato:wght@300;400;700&display=swap">
<style>
  :root{
    --stage:#555555;
    --slide:#f6f6f6;
    --orange:#f0901f;
    --orange-deep:#e2861c;
    --navy:#222b3a;
    --ink:#3d3d3d;
    --white:#ffffff;
  }
  *{margin:0;padding:0;box-sizing:border-box}
  html,body{width:1200px;height:960px;overflow:hidden;background:var(--stage)}
  body{position:relative;font-family:"Lato",sans-serif;color:var(--ink)}
  .page-label{position:absolute;top:74px;left:0;width:1172px;text-align:center;color:var(--white);font-weight:300;font-size:26px}
  .slide{position:absolute;left:111px;top:135px;width:970px;height:728px;background:radial-gradient(ellipse at 50% 40%,#fdfdfd 0%,var(--slide) 60%,#efefef 100%);overflow:hidden}
  .slide-bands{position:absolute;inset:0}
  .slide-title{position:absolute;left:30px;top:62px;font-weight:300;font-size:38px;color:var(--white);letter-spacing:.2px}
  .brand{position:absolute;right:34px;top:67px;display:flex;align-items:center;gap:9px;color:var(--white);font-weight:700;font-size:24px}
  .brand-dot{width:16px;height:16px;border-radius:50%;background:var(--orange)}
  .hero-visual{position:absolute;left:81px;top:193px;width:344px;height:248px;border-radius:6px;background:radial-gradient(ellipse at 50% 45%,#3f9be0 0%,#2f7cc7 45%,#c9d3dc 80%,transparent 100%)}
  .lead{position:absolute;left:58px;top:473px;width:404px;font-size:18px;line-height:22.6px;text-align:justify}
  .points{position:absolute;left:521px;top:216px;width:420px;list-style:none}
  .points li{position:relative;padding-left:25px;font-size:19.5px;line-height:29px;margin-bottom:29px}
  .points li::before{content:"";position:absolute;left:0;top:10px;width:10px;height:10px;background:var(--orange)}
  .footer-text{position:absolute;left:26px;top:694px;font-size:13px;color:var(--white);font-weight:300}
  .footer-text .sep{margin:0 6px}
</style>
</head>
<body>
  <div class="page-label">Page 4</div>
  <section class="slide">
    <svg class="slide-bands" width="970" height="728" viewBox="0 0 970 728" aria-hidden="true">
      <polygon points="749,33 970,33 970,42 740,42" fill="var(--orange)"/>
      <polygon points="0,46 740,46 661,122 0,122" fill="var(--orange)"/>
      <polygon points="560,46 740,46 700,84 520,84" fill="#f49a2e" opacity=".55"/>
      <polygon points="0,122 0,106 620,106 640,122" fill="#f3a443" opacity=".35"/>
      <polygon points="747,46 970,46 970,122 667,122" fill="var(--navy)"/>
      <polygon points="0,125 662,125 653,135 0,135" fill="var(--navy)"/>
      <polygon points="0,689 276,689 248,717 0,717" fill="var(--navy)"/>
      <polygon points="280,689 970,689 970,717 252,717" fill="var(--orange-deep)"/>
    </svg>
    <h1 class="slide-title">Title Goes Here</h1>
    <div class="brand"><span class="brand-dot"></span>Bold Ledger</div>
    <div class="hero-visual" role="img" aria-label="Laptop surrounded by colourful floating app icons"></div>
    <p class="lead">Duis autem vel eum iriure dolor in hendrerit in vulputate velit esse molestie consequat, vel illum dolore eu feugiat nulla facilisis at vero eros et accumsan et iusto odio dignissim qui blandit praesent luptatum zzril delenit augue duis dolore te feugait nulla facilisi.</p>
    <ul class="points">
      <li>Souvlaki ignitus carborundum e pluribus unum.</li>
      <li>Defacto lingo est igpay atinlay. Marquee selectus non provisio.</li>
      <li>Quote meon an estimate et non interruptus stadium.</li>
      <li>Sic tempus fugit esperanto hiccup estrogen.</li>
      <li>Epsum factorial non deposit quid pro quo hic escorol.</li>
    </ul>
    <div class="footer-text">www.boldledger.com<span class="sep">|</span>Page 2</div>
  </section>
</body>
</html>
```